Business Cards for IT Consulting Company (Managed Service Provider)

I am looking to have some business cards printed and would like some designs. We are an IT Consulting company based in Vancouver BC. I would like a nice clean and modern look to the cards. I have uploaded all the versions of my logo so parts can be used as needed. Here is a snippit from our website homepage:

Quillbrook Networks Ltd. is an IT Solutions Partner located in Vancouver BC, Canada. We offer IT solutions and support to customers in the greater Vancouver Area. With expertise in Microsoft platforms, as well as Linux and Mac OSX and over 12 years experience in the IT industry, Quillbrook Networks is dedicated to offering our clients top quality service and products. We take pride in the solutions we offer our customers. The greatest compliment a client can give us is to recommend our services.

Quillbrook Networks Ltd. offers a wide range of IT services from onsite service to remote support and managed service solutions. This allows clients to choose the support path that best suits their company’s needs. Supporting many different sized companies from small to enterprise level over the past 12 years Quillbrook Networks has the experience and expertise needed to ensure things run smoothly. Allowing our clients to focus on doing business.

Revolutionizing the way IT services are delivered.

Quillbrook Networks is dedicated to providing our clients with IT solutions that work and grow with them for years to come. This philosophy helps save money in the long run instead of replacing equipment constantly. Far too often IT solutions are not well thought out and while possibly solving the problem at hand, require replacement due to growth or quality within a very short time frame. Quillbrook Networks takes pride in providing solutions that will last and be able to accommodate growth without the need for replacement.

Industry/Entity Type

Information Technology

Contact Information for Business Card

Quillbrook Networks Ltd.
(Employee Name)
Eml: (Employees Email Address)
Web: quillbrook.me
Ph: 604-555-0148

Font styles to use
Serif
Sans Serif

Requirements
Must have
• The Company logo and company colors.
Nice to have
• - Our tag line: "Revolutionizing IT Services" or "Revolutionizing the way IT services are delivered."
• - Also I really like the idea of nature and technology together blending which is sort of where my logo came from so integrating that somehow onto the business cards would be great.

```html
<!DOCTYPE html>
<html lang="en">
<head>
<meta charset="utf-8">
<title>Quillbrook Networks Ltd. — Business Cards</title>
<link rel="stylesheet" href="https://fonts.googleapis.com/css2?family=Montserrat:wght@500&family=Roboto:ital,wght@0,400;0,500;1,400&display=swap">
<style>
  :root {
    --backdrop: #a3a0a0;
    --brand-blue: #1b90d6;
    --card-white: #f2f2f2;
    --ink: #3a3a3a;
    --ink-soft: #444444;
    --rule: #d6d6d6;
    --on-blue: #ffffff;
  }
  * { margin: 0; padding: 0; box-sizing: border-box; }
  html, body {
    width: 1200px;
    height: 1200px;
    overflow: hidden;
    background: var(--backdrop);
  }
  .canvas {
    position: relative;
    width: 1200px;
    height: 1200px;
  }
  .card {
    position: absolute;
    width: 713px;
    height: 418px;
  }

  /* Front */
  .card--front {
    left: 238px;
    top: 118px;
    background: var(--brand-blue);
  }
  .card-front__pattern {
    position: absolute;
    inset: 0;
    background: var(--brand-blue);
  }
  .front-name {
    position: absolute;
    left: 112px;
    top: 148px;
    color: var(--on-blue);
    font-family: "Montserrat", sans-serif;
    font-weight: 500;
    line-height: 1;
  }
  .front-name__main {
    display: block;
    font-size: 68px;
    letter-spacing: -0.5px;
  }
  .front-name__sub {
    display: block;
    margin-top: 12px;
    margin-left: 4px;
    font-size: 25px;
    letter-spacing: 1px;
  }

  /* Back */
  .card--back {
    left: 230px;
    top: 645px;
    background: var(--card-white);
  }
  .back-name {
    position: absolute;
    left: 58px;
    top: 186px;
    width: 280px;
    color: var(--brand-blue);
    font-family: "Montserrat", sans-serif;
    font-weight: 500;
    font-size: 34px;
    line-height: 1;
  }
  .back-divider {
    position: absolute;
    left: 341px;
    top: 83px;
    width: 1px;
    height: 248px;
    background: var(--rule);
  }
  .contact {
    position: absolute;
    left: 400px;
    top: 129px;
    font-family: "Roboto", sans-serif;
  }
  .contact__name {
    color: var(--brand-blue);
    font-weight: 500;
    font-size: 25px;
    line-height: 1;
  }
  .contact__role {
    margin-top: 8px;
    color: var(--ink-soft);
    font-style: italic;
    font-size: 16px;
  }
  .contact__list {
    list-style: none;
    margin-top: 26px;
  }
  .contact__item {
    display: flex;
    align-items: center;
    height: 27px;
    color: var(--ink);
    font-size: 18px;
  }
  .contact__icon {
    width: 18px;
    height: 16px;
    margin-right: 18px;
    fill: var(--brand-blue);
    flex: none;
  }
</style>
</head>
<body>
<main class="canvas">

  <section class="card card--front" aria-label="Business card front">
    <div class="card-front__pattern" role="img" aria-label="Subtle tonal geometric pattern on brand blue"></div>
    <h1 class="front-name">
      <span class="front-name__main">Quillbrook</span>
      <span class="front-name__sub">NETWORKS LTD.</span>
    </h1>
  </section>

  <section class="card card--back" aria-label="Business card back">
    <p class="back-name">Quillbrook</p>
    <div class="back-divider"></div>
    <div class="contact">
      <h2 class="contact__name">Daniel Hart</h2>
      <p class="contact__role">Managing Director</p>
      <ul class="contact__list">
        <li class="contact__item">
          <svg class="contact__icon" viewBox="0 0 18 16" aria-hidden="true">
            <path d="M2 4 Q9 0 16 4 L15 6.5 L12 6 L11.5 4.5 Q9 4 6.5 4.5 L6 6 L3 6.5 Z"/>
            <path d="M4 8 L14 8 L16 15 L2 15 Z"/>
          </svg>
          <span>604-555-0148</span>
        </li>
        <li class="contact__item">
          <svg class="contact__icon" viewBox="0 0 18 16" aria-hidden="true">
            <circle cx="9" cy="8" r="7"/>
            <path d="M2 8 H16 M9 1 V15 M4 3.5 Q9 6 14 3.5 M4 12.5 Q9 10 14 12.5 M9 1 Q5 8 9 15 M9 1 Q13 8 9 15" stroke="#f2f2f2" stroke-width="1" fill="none"/>
          </svg>
          <span>www.quillbrook.me</span>
        </li>
        <li class="contact__item">
          <svg class="contact__icon" viewBox="0 0 18 16" aria-hidden="true">
            <rect x="1" y="3" width="16" height="11"/>
            <path d="M1 3 L9 9.5 L17 3 M1 14 L7 8 M17 14 L11 8" stroke="#f2f2f2" stroke-width="1.2" fill="none"/>
          </svg>
          <span>support@quillbrook.me</span>
        </li>
      </ul>
    </div>
  </section>

</main>
</body>
</html>
```